Interior Stylist business card design needed

I need a business card for my new company in Sydney called "Liv Harrowby Designs". The business offers an interior styling and colour consultancy. My clients are generally not very design savvy (hence why they use me) and can range from being quite conservative to really wanting something "out there". They can be looking for a budget makeover or something more expensive / substantial. I'd like my business card design to be stylish (but not overly formal). I certainly don't want it to be conservative. I'd like it to stand out a bit! I don't really have any aversion to particular colours and I don't have a logo as such - my business name is really all I have.

Target Market(s)

As above - home owners, ranging from conservative to modern

Industry/Entity Type

Conservative

Contact Information for Business Card

Liv Harrowby Designs
Colour consultancy and interior styling
ph: 0417 238 605
email: livharrowby@qoralnet.net.au

Requirements
Should not have
• Old fashioned writing or motifs. No Times Roman font!!

```html
<!DOCTYPE html>
<html lang="en">
<head>
<meta charset="utf-8">
<title>Liv Harrowby Designs – Business Card</title>
<link href="https://fonts.googleapis.com/css2?family=Open+Sans:wdth,wght@75..100,300..700&display=swap" rel="stylesheet">
<style>
  :root {
    --page: #ffffff;
    --card-yellow: #fdc90a;
    --ink: #111111;
    --tone-orange: #f26522;
    --tone-red: #e8312a;
    --tone-green: #1fa94e;
    --tone-aqua: #5fc2cf;
    --tone-blue: #4aa8d0;
    --tone-slate: #7c8aa2;
  }
  * { margin: 0; padding: 0; box-sizing: border-box; }
  html, body {
    width: 1200px;
    height: 741px;
    overflow: hidden;
    background: var(--page);
  }
  .card {
    position: absolute;
    left: 0;
    top: 22px;
    width: 1200px;
    height: 694px;
    background: var(--card-yellow);
    overflow: hidden;
  }
  .colour-artwork {
    position: absolute;
    left: 705px;
    top: 58px;
    width: 495px;
    height: 566px;
    background: linear-gradient(
      to bottom,
      var(--tone-orange) 0%,
      var(--tone-red) 28%,
      var(--tone-green) 52%,
      var(--tone-aqua) 74%,
      var(--tone-blue) 88%,
      var(--tone-slate) 100%
    );
  }
  .identity {
    position: absolute;
    left: 100px;
    width: 600px;
    text-align: center;
    color: var(--ink);
  }
  .business-name {
    top: 226px;
    font-family: "Open Sans", sans-serif;
    font-weight: 700;
    font-size: 52px;
    line-height: 1;
  }
  .tagline {
    top: 292px;
    font-family: "Open Sans", sans-serif;
    font-stretch: 75%;
    font-weight: 300;
    font-size: 29px;
    line-height: 1;
  }
  .contact {
    font-family: "Open Sans", sans-serif;
    font-weight: 300;
    font-size: 36px;
    line-height: 1;
  }
  .phone { top: 412px; }
  .email { top: 492px; }
</style>
</head>
<body>
  <div class="card">
    <div class="colour-artwork" role="img" aria-label="Painted brushstroke colour swatches in orange, red, green, aqua, blue and slate"></div>
    <h1 class="identity business-name">Liv Harrowby Designs</h1>
    <p class="identity tagline">Colour Consultancy &amp; Interior Styling</p>
    <p class="identity contact phone">0417 238 605</p>
    <p class="identity contact email">livharrowby@qoralnet.net.au</p>
  </div>
</body>
</html>
```